Realty Group Needs Classy, Contemporary Letterhead Design

We need a letterhead design for a new realty company located in NY, USA. We buy investment properties to rehabilitate and or keep in our rental portfolio.

```html
<!DOCTYPE html>
<html lang="en">
<head>
<meta charset="utf-8">
<title>Meridian Realty Group – Letterhead</title>
<link rel="stylesheet" href="https://fonts.googleapis.com/css2?family=Open+Sans:wght@400;500;600&family=Lato:wght@400&display=swap">
<style>
  :root {
    --purple: #4f2b85;
    --grey: #7d7d7d;
    --ink: #3f3f3f;
    --paper: #ffffff;
    --backdrop: #e6e6e6;
  }
  html, body {
    margin: 0;
    padding: 0;
    width: 1040px;
    height: 1200px;
    overflow: hidden;
    background: var(--backdrop);
  }
  .letterhead {
    position: absolute;
    left: 69px;
    top: 20px;
    width: 798px;
    height: 1027px;
    background: var(--paper);
    transform: scale(1.1295);
    transform-origin: top left;
    font-family: "Open Sans", sans-serif;
    color: var(--ink);
    overflow: hidden;
  }
  .header-shape, .footer-shape { position: absolute; left: 0; display: block; }
  .header-shape { top: 0; }
  .footer-shape { bottom: 0; }
  .company-name {
    position: absolute;
    right: 92px;
    top: 72px;
    margin: 0;
    font-family: "Open Sans", sans-serif;
    font-weight: 600;
    font-size: 17px;
    line-height: 1.2;
    color: var(--purple);
    white-space: nowrap;
  }
  .letter-body {
    position: absolute;
    left: 75px;
    top: 201px;
    width: 645px;
    font-size: 12.2px;
  }
  .meta { margin: 0 0 14px; line-height: 15px; }
  .recipient { margin: 0 0 43px; line-height: 15.5px; }
  .salutation { margin: 0 0 24px; }
  .paragraph {
    margin: 0 0 23px;
    line-height: 23px;
    text-align: justify;
    hyphens: auto;
  }
  .closing { margin: 46px 0 8px; }
  .signature-mark {
    width: 184px;
    height: 22px;
    background: linear-gradient(90deg, rgba(80,80,80,0.18), rgba(80,80,80,0.06));
    border-radius: 3px;
  }
  .signer-name { margin: 9px 0 0; font-size: 15px; font-weight: 500; color: #333; }
  .signer-role { margin: 5px 0 0; font-size: 12.2px; }
  .footer-address {
    position: absolute;
    left: 75px;
    top: 961px;
    font-family: "Lato", sans-serif;
    font-size: 15px;
    color: #222;
  }
  .contact-list {
    position: absolute;
    left: 533px;
    top: 936px;
    margin: 0;
    padding: 0;
    list-style: none;
    font-family: "Lato", sans-serif;
    font-size: 15px;
    color: var(--paper);
    line-height: 19px;
  }
  .contact-list li { display: flex; align-items: center; gap: 9px; }
  .contact-list svg { width: 15px; height: 15px; fill: var(--paper); }
</style>
</head>
<body>
  <main class="letterhead" lang="en">
    <svg class="header-shape" width="798" height="130" viewBox="0 0 798 130" aria-hidden="true">
      <rect x="330" y="8" width="468" height="22" fill="var(--grey)"/>
      <path d="M0 0 H798 V8 H420 C385 8 368 18 345 45 C300 100 285 125 230 125 H0 Z" fill="var(--purple)"/>
    </svg>

    <p class="company-name">Meridian Realty Group, LLC</p>

    <section class="letter-body">
      <p class="meta">Issuing Date: May 5, 2018</p>
      <p class="recipient">Name Of Employee Mr. XYZABC<br>Address of Employee<br>Address Line 2 etc..</p>
      <p class="salutation">Dear Mr.XYZABC</p>
      <p class="paragraph">Lorem Ipsum has been the industry's standard dummy text ever since the 1500s, when an unknown printer took a galley of type and scrambled it to make a type specimen book. It has survived not only five centuries, but also the leap into electronic typesetting, remaining essentially unchanged. It was popularised in the 1960s with the release of Letraset sheets containing Lorem Ipsum passages, and more recently with desktop publishing software like Aldus PageMaker including versions of Lorem Ipsum.</p>
      <p class="paragraph">Lorem Ipsum is simply dummy text of the printing and typesetting industry. Lorem Ipsum has been the industry's standard dummy text ever since the 1500s, when an unknown printer took a galley of type and scrambled it to make a type specimen book.</p>
      <p class="paragraph">It has survived not only five centuries, but also the leap into electronic typesetting, remaining essentially unchanged. It was popularised in the 1960s with the release of Letraset sheets containing Lorem IpsumIpsum passages.</p>
      <p class="closing">Yours Sincerely</p>
      <div class="signature-mark" role="img" aria-label="Handwritten signature of Daniel Harper"></div>
      <p class="signer-name">Daniel Harper</p>
      <p class="signer-role">Managing Director</p>
    </section>

    <svg class="footer-shape" width="798" height="134" viewBox="0 0 798 134" aria-hidden="true">
      <rect x="0" y="95" width="500" height="22" fill="var(--grey)"/>
      <path d="M0 117 H400 C440 117 452 104 470 80 C505 30 525 0 570 0 H798 V134 H0 Z" fill="var(--purple)"/>
    </svg>

    <div class="footer-address">421, Address line here Country Name, 45452</div>

    <ul class="contact-list">
      <li>
        <svg viewBox="0 0 16 16" aria-hidden="true"><path d="M1 5 C1 2 4 2 8 2 C12 2 15 2 15 5 L11.5 5.5 L11 4 H5 L4.5 5.5 Z M4 7 H12 L14 13 H2 Z M8 8.5 A2 2 0 1 0 8.01 8.5 Z"/></svg>
        044-123 456 789
      </li>
      <li>
        <svg viewBox="0 0 16 16" aria-hidden="true"><path d="M1 3 H15 V13 H1 Z M2.5 4.5 L8 9 L13.5 4.5 V11.5 H2.5 Z" fill-rule="evenodd"/></svg>
        info@webname.com
      </li>
      <li>
        <svg viewBox="0 0 16 16" aria-hidden="true"><circle cx="8" cy="8" r="7"/><path d="M4 5 C6 4 7 6 6 8 C5 10 7 11 7 13 M10 3 C9 5 11 6 12 7" stroke="var(--purple)" stroke-width="1.4" fill="none"/></svg>
        www.websitename.com
      </li>
    </ul>
  </main>
</body>
</html>
```